New Business Card Design Project

We require a business card design for Vexalund, a newly established Indian company.
Our focus is on the development, manufacturing, and export of a diverse array of pharmaceutical products on a global scale. The card should convey a professional appearance, as our primary markets are in Africa, China, and Southeast Asian nations.
We envision a two-sided business card, with the reverse side dedicated to a logo set against a solid color or an elegantly designed pattern. The corners should be rounded. We would appreciate seeing both horizontal and vertical design options. We trust the designer to utilize their expertise in creating this design.

The content for the business card is included in the attached Word file.

Target Market(s)

Our primary markets are in Africa, China, and Southeast Asian, Latin America, Maldives, Sri Lanka

Industry/Entity Type

Pharmaceutical Manufacturing and Export

Contact Information for Business Card

Colors

Designer to choose colors to be used in the design.

Requirements
Must have
• The reverse side of the business card features solely the logo along with the tagline, "Remedies of Life."
Should not have
• The logo should not exceed two instances, encompassing both the front and back sides of the card.

```html
<!DOCTYPE html>
<html lang="en">
<head>
<meta charset="utf-8">
<title>Vexalund Business Card</title>
<link href="https://fonts.googleapis.com/css2?family=Poppins:wght@300;400;600;700&display=swap" rel="stylesheet">
<style>
  :root {
    --page-bg: #d8d3cb;
    --card-bg: #f1f2f1;
    --card-edge: #dfe2e1;
    --brand-blue: #1d9bd2;
    --teal: #17839f;
    --red: #e6463a;
    --dark: #1e1d1d;
    --ink: #222222;
    --light-text: #e4e1dc;
  }
  html, body {
    margin: 0;
    padding: 0;
    width: 1200px;
    height: 887px;
    overflow: hidden;
    background: var(--page-bg);
    font-family: "Poppins", sans-serif;
  }
  .business-card {
    position: absolute;
    left: 100px;
    top: 170px;
    width: 1000px;
    height: 546px;
    border-radius: 24px;
    overflow: hidden;
    background: linear-gradient(160deg, #f7f8f7 0%, var(--card-bg) 60%, #e7e9e8 100%);
    box-shadow: 0 0 0 1px var(--card-edge);
  }
  .card-art { position: absolute; inset: 0; }
  .company-name { font-weight: 600; font-size: 62px; fill: var(--brand-blue); }
  .person-first { font-weight: 700; font-size: 40px; fill: var(--teal); letter-spacing: 1px; }
  .person-last { font-weight: 700; font-size: 40px; fill: var(--red); letter-spacing: 1px; }
  .person-title { font-weight: 400; font-size: 22px; fill: var(--ink); }
  .contact-line { font-weight: 300; font-size: 23px; fill: var(--light-text); }
  .address-line { font-weight: 400; font-size: 23px; fill: var(--light-text); }
  .contact-icon { fill: none; stroke: var(--brand-blue); stroke-width: 1.8; }
</style>
</head>
<body>
  <div class="business-card">
    <svg class="card-art" viewBox="0 0 1000 546" width="1000" height="546">
      <!-- bands -->
      <path class="band-blue" fill="var(--brand-blue)" d="M0,385 C150,400 330,380 500,318 C350,398 170,428 0,422 Z"/>
      <path class="band-red" fill="var(--red)" d="M0,434 C200,450 420,380 620,285 C780,215 900,215 965,235 C880,228 770,252 640,307 C450,397 220,472 0,468 Z"/>
      <path class="band-dark" fill="var(--dark)" d="M0,486 C230,482 440,402 640,320 C790,260 900,246 1000,270 L1000,546 L0,546 Z"/>

      <!-- brand -->
      <text class="company-name" x="50" y="290">Vexalund</text>

      <!-- person -->
      <text x="946" y="92" text-anchor="end"><tspan class="person-first">TAMSIN </tspan><tspan class="person-last">HOLLOWAY</tspan></text>
      <text class="person-title" x="946" y="122" text-anchor="end">Founder &amp; Principal</text>
      <rect class="accent-bar" x="961" y="58" width="15" height="60" fill="var(--teal)"/>

      <!-- contacts -->
      <text class="contact-line" x="916" y="323" text-anchor="end">+1- 415-555-0193</text>
      <text class="contact-line" x="916" y="354" text-anchor="end">info@vexalund.com</text>
      <text class="contact-line" x="916" y="385" text-anchor="end">www.vexalund.com</text>

      <path class="contact-icon" d="M930,305 q-3,3 0,9 l5,7 q4,4 8,1 l-3,-4 q-2,1 -4,-2 l-3,-5 q-1,-2 1,-3 z"/>
      <rect class="contact-icon" x="928" y="341" width="15" height="11" rx="1"/>
      <path class="contact-icon" d="M928,342 l7.5,6 l7.5,-6"/>
      <circle class="contact-icon" cx="936" cy="378" r="8"/>
      <ellipse class="contact-icon" cx="936" cy="378" rx="3.5" ry="8"/>
      <path class="contact-icon" d="M928,378 h16 M929.5,374 h13 M929.5,382 h13"/>

      <!-- address -->
      <text class="address-line" x="946" y="446" text-anchor="end">4817 Linden Grove Avenue</text>
      <text class="address-line" x="946" y="477" text-anchor="end">#27, Suite Harbor Point</text>
    </svg>
  </div>
</body>
</html>
```